VFX Company Business Card Design Project

The Kestrel Works is a decentralized Visual Effects Studio servicing the television and feature film industries.
Project Brief:
Take our logo that was previously designed on Pencil Harbor and make a double sided business card.
Requirements:
- Card MUST be double sided.
- Front of card MUST have the yellow part of our logo against the dark grey background.
- Back of card is completely up to the designer.
- Back of card must include the complete company logo.
Please follow these File Preparation guidelines:
http://printnook.ca/infopage?file=filetype_en&s=PrintNook_new&lang=en
Business

```html
<!DOCTYPE html>
<html lang="en">
<head>
<meta charset="utf-8">
<title>The Kestrel Works — Business Card</title>
<link rel="stylesheet" href="https://fonts.googleapis.com/css2?family=Jost:wght@300;400;500;600&display=swap">
<style>
  :root {
    --stage: #e9e4dc;
    --label: #1c1c1c;
    --card: #2b2b2b;
    --slate: #5f6d70;
    --ink-light: #f2f2f2;
    --mark-grey: #d9dcdc;
    --yellow: #fcc325;
  }
  * { box-sizing: border-box; margin: 0; padding: 0; }
  html, body { width: 1200px; height: 788px; overflow: hidden; }
  body {
    position: relative;
    background: var(--stage);
    font-family: "Jost", "Helvetica Neue", Arial, sans-serif;
    color: var(--ink-light);
  }
  .view-label {
    position: absolute;
    font-size: 22px;
    font-weight: 400;
    color: var(--label);
    transform: translateX(-50%);
    white-space: nowrap;
  }
  .card {
    position: absolute;
    width: 524px;
    height: 300px;
    background: var(--card);
    border-radius: 18px;
    overflow: hidden;
  }
  .card--back { left: 338px; top: 78px; }
  .card--front-mark { left: 54px; top: 446px; }
  .card--front-lockup { left: 622px; top: 446px; }

  /* back */
  .back-name {
    position: absolute; left: 28px; top: 46px;
    font-size: 36px; font-weight: 500; color: var(--mark-grey);
    letter-spacing: 0.5px;
  }
  .holder {
    position: absolute; left: 27px; top: 134px;
    font-size: 20px; font-weight: 300; letter-spacing: 0.6px;
  }
  .holder small { font-size: 14px; letter-spacing: 0.8px; }
  .contact {
    position: absolute; left: 27px; font-size: 13px; font-weight: 400;
    letter-spacing: 0.2px;
  }
  .contact b { font-weight: 600; font-style: italic; }
  .contact--phones { top: 176px; }
  .contact--web { top: 196px; }
  .footer-band {
    position: absolute; left: 0; right: 0; bottom: 0; height: 84px;
    background: linear-gradient(to bottom, var(--card) 0%, var(--slate) 40%, var(--slate) 100%);
  }
  .address {
    position: absolute; right: 18px; top: 248px;
    font-size: 13px; line-height: 18px; text-align: right;
  }

  /* fronts */
  .front-name {
    position: absolute; left: 0; right: 0; top: 122px;
    text-align: center; font-size: 46px; font-weight: 500;
    color: var(--yellow); letter-spacing: 0.5px;
  }
  .lockup {
    position: absolute; left: 0; right: 0; top: 128px;
    display: flex; align-items: center; justify-content: center; gap: 16px;
  }
  .lockup-dot { width: 30px; height: 30px; border-radius: 50%; background: var(--yellow); }
  .lockup-name { font-size: 34px; font-weight: 500; color: var(--mark-grey); }
  .site {
    position: absolute; left: 0; right: 0; top: 254px;
    text-align: center; font-size: 22px; font-weight: 400; letter-spacing: 4px;
  }
</style>
</head>
<body>
  <div class="view-label" style="left:600px; top:32px;">Back</div>
  <div class="view-label" style="left:327px; top:403px;">Front - 1</div>
  <div class="view-label" style="left:900px; top:403px;">Front - 2</div>

  <section class="card card--back">
    <div class="back-name">The Kestrel Works</div>
    <div class="holder">Your Name, <small>Designation</small></div>
    <div class="contact contact--phones"><b>cell</b> 123-456-7890 &nbsp;|&nbsp; <b>phone</b> 123-456-7890</div>
    <div class="contact contact--web"><b>email</b> info@website.com &nbsp;|&nbsp; <b>web</b> www.website.com</div>
    <div class="footer-band" role="img" aria-label="Decorative slate and cream wave band along the card's lower edge"></div>
    <div class="address">0000#, Area Name<br>State Name, Country code</div>
  </section>

  <section class="card card--front-mark">
    <div class="front-name">The Kestrel Works</div>
    <div class="site">www.website.com</div>
  </section>

  <section class="card card--front-lockup">
    <div class="lockup">
      <span class="lockup-dot"></span>
      <span class="lockup-name">The Kestrel Works</span>
    </div>
    <div class="site">www.website.com</div>
  </section>
</body>
</html>
```